3 Page Design for Ninth Bay Capital

We want a Home Page, About Page, and Products & Services Page for Ninth Bay Capital. Please refer to the attached docs for more info.
If done in Figma, would like Figma files that can easily be ported to Wordpress.

```html
<!DOCTYPE html>
<html lang="en">
<head>
<meta charset="utf-8">
<title>Ninth Bay Capital — Home</title>
<link rel="stylesheet" href="https://fonts.googleapis.com/css2?family=Archivo:wght@500;600;700;800&family=Arimo:wght@400;700&display=swap">
<style>
:root{
  --ink:#1e1e1e;
  --muted:#555;
  --sand:#e8dcc8;
  --sand-btn:#e6d8c2;
  --paper:#f7f7f7;
  --white:#fff;
  --navy:#14183a;
  --footer:#262626;
  --home:#e9d9bd;
}
*{margin:0;padding:0;box-sizing:border-box}
html,body{width:1200px;height:3571px;overflow:hidden}
body{position:relative;font-family:"Arimo",Arial,sans-serif;color:var(--ink);background:var(--white)}
.abs{position:absolute}
.h{font-family:"Archivo",Arial,sans-serif;font-weight:700;text-transform:uppercase;letter-spacing:.2px}
.btn{position:absolute;display:flex;align-items:center;justify-content:center;gap:8px;background:var(--sand-btn);font-size:17px;color:var(--ink);border-radius:2px;text-transform:uppercase;white-space:nowrap}
.btn svg{width:13px;height:13px}
.eyebrow{font-size:16px;text-transform:uppercase}
/* header */
.site-header{top:0;left:0;width:1200px;height:84px;background:var(--white)}
.brand{left:101px;top:25px;display:flex;align-items:center;gap:10px;font-family:"Archivo",sans-serif;font-weight:700;font-size:15px;text-transform:uppercase}
.brand-dot{width:34px;height:34px;border-radius:50%;background:var(--ink)}
.nav a{position:absolute;top:32px;font-size:17px;color:var(--ink);text-decoration:none}
.nav .active{color:var(--home)}
.talk{left:940px;top:24px;display:flex;gap:8px;align-items:center}
.talk small{display:block;font-size:10px}
.talk b{font-weight:400;font-size:17px}
/* hero */
.hero{top:84px;left:0;width:1200px;height:640px;overflow:hidden}
.hero-photo{position:absolute;inset:0;background:linear-gradient(100deg,#5d5d5f 0%,#7b7b7e 40%,#8a8a8c 60%,#8b4c45 100%)}
.hero-copy{left:101px;top:198px;color:var(--white);width:460px}
.hero-copy h1{font-size:39px;line-height:45px;margin:12px 0 14px}
.hero-copy p{font-size:16px;line-height:22px}
.socials{left:40px;top:169px;display:flex;flex-direction:column;gap:9px}
.socials span{width:22px;height:22px;border:1.3px solid var(--white);border-radius:50%}
.scroll{left:44px;top:456px;color:var(--white);font-size:9px;letter-spacing:4px;transform:rotate(-90deg);transform-origin:left top;white-space:nowrap}
/* welcome */
.welcome{top:720px;left:0;width:1200px;height:589px;background:var(--paper)}
.welcome-ring{left:112px;top:42px;width:466px;height:466px;border-radius:50%;background:var(--sand)}
.welcome-photo{left:112px;top:56px;width:466px;height:466px;border-radius:50%;background:radial-gradient(circle at 55% 45%,#6d6d70,#2c2c30 80%)}
.welcome-copy{left:633px;top:108px;width:470px}
.welcome-copy h2{font-size:31px;margin:12px 0 10px}
.lead{font-weight:700;font-size:16px;line-height:23px;margin-bottom:18px}
.body{font-size:14.5px;line-height:24.5px;color:#333}
/* services */
.services{top:1309px;left:0;width:1200px;height:679px;text-align:center}
.services h2{font-size:31px;margin:8px 0 8px}
.card{position:absolute;top:182px;width:322px;text-align:left}
.card .pic{height:333px}
.card h3{font-family:"Archivo",sans-serif;font-weight:600;font-size:20px;margin:16px 0 6px}
.card p{font-size:15.5px;line-height:25px;color:#333}
/* discipline */
.discipline{top:1988px;left:0;width:1200px;height:454px;background:var(--sand)}
.discipline-photo{left:600px;top:0;width:600px;height:454px;background:linear-gradient(120deg,#6d8990,#3f6a73 45%,#b9c4c8)}
.discipline-copy{left:101px;top:126px;width:470px}
.discipline-copy h2{font-size:32px;line-height:37px;margin-bottom:16px}
.discipline-copy p{font-size:14.5px;line-height:21px}
.btn.outline{background:none;border:1.3px solid var(--ink)}
/* why */
.why{top:2442px;left:0;width:1200px;height:572px}
.why-photo{left:101px;top:58px;width:474px;height:452px;background:linear-gradient(160deg,#dcdad6,#a9a49c 60%,#8a847b)}
.why-frame{left:118px;top:70px;width:441px;height:424px;border:1px solid rgba(255,255,255,.8)}
.why-copy{left:636px;top:94px;width:464px}
.why-copy h2{font-size:31px;margin:10px 0 10px}
.why-copy .intro{font-size:15.5px;line-height:19px;color:#777;text-align:justify;margin-bottom:14px}
.why-copy dt{font-weight:700;font-size:16px;margin-top:18px}
.why-copy dt:first-child{margin-top:0}
.why-copy dd{font-size:16px;margin-top:8px}
/* contact */
.contact{top:3014px;left:0;width:1200px;height:486px;background:var(--sand)}
.contact-copy{left:118px;top:98px;width:360px}
.contact-copy h2{font-size:38px;margin:4px 0 8px}
.contact-copy .sub{font-size:17px;line-height:22px}
.info{display:flex;gap:14px;align-items:flex-start;font-size:17px;line-height:22px;margin-top:28px}
.info svg{width:18px;height:18px;flex:none;margin-top:2px}
.form{left:583px;top:55px;width:521px;height:384px;background:var(--white);border-radius:12px}
.form h3{position:absolute;left:28px;top:40px;font-family:"Archivo",sans-serif;font-weight:700;font-size:38px;color:var(--navy)}
.field{position:absolute;border:1px solid #d9d9d9;border-radius:2px;font-size:14px;padding:14px;color:#333}
/* footer */
.site-footer{top:3500px;left:0;width:1200px;height:71px;background:var(--footer);color:var(--white);font-size:17px;display:flex;align-items:center;justify-content:center}
</style>
</head>
<body>
<header class="abs site-header">
  <div class="abs brand"><span class="brand-dot"></span>Ninth Bay Capital</div>
  <nav class="nav">
    <a class="active" style="left:418px">HOME</a>
    <a style="left:513px">ABOUT US</a>
    <a style="left:642px">SERVICES</a>
  </nav>
  <div class="btn" style="left:762px;top:25px;width:157px;height:36px">CONTACT US <svg viewBox="0 0 12 12"><path d="M2 10L10 2M4 2h6v6" fill="none" stroke="currentColor" stroke-width="1.4"/></svg></div>
  <div class="abs talk">
    <svg width="26" height="26" viewBox="0 0 24 24"><path d="M5 3l4 1 1 4-2 2a12 12 0 0 0 6 6l2-2 4 1 1 4-2 2C10 21 3 14 3 5z" fill="none" stroke="#1e1e1e" stroke-width="1.3"/></svg>
    <div><small>TALK WITH US</small><b>+1 555 014 2290</b></div>
  </div>
</header>

<section class="abs hero">
  <div class="hero-photo" role="img" aria-label="Sprinter launching from starting blocks on a stadium track under cloudy sky"></div>
  <svg class="abs" style="left:0;top:560px" width="1200" height="80" viewBox="0 0 1200 80" preserveAspectRatio="none">
    <path d="M0 0 Q600 100 1200 0 V80 H0Z" fill="var(--sand)"/>
    <path d="M0 18 Q600 112 1200 18 V80 H0Z" fill="var(--paper)"/>
  </svg>
  <div class="abs socials"><span></span><span></span><span></span><span></span></div>
  <div class="abs" style="left:50px;top:276px;width:1px;height:40px;background:#fff"></div>
  <div class="abs scroll">SCROLL DOWN</div>
  <div class="abs hero-copy">
    <div class="eyebrow">Ninth Bay Capital</div>
    <h1 class="h">Life after the game<br>has a strategy</h1>
    <p>We guide athletes and entrepreneurs into long-term wealth clarity. Built for legacy—designed for performance.</p>
  </div>
  <div class="btn" style="left:101px;top:391px;width:166px;height:36px">GET STARTED <svg viewBox="0 0 12 12"><path d="M2 10L10 2M4 2h6v6" fill="none" stroke="currentColor" stroke-width="1.4"/></svg></div>
</section>

<section class="abs welcome">
  <div class="abs welcome-ring"></div>
  <div class="abs welcome-photo" role="img" aria-label="Woman presenting notes on a glass board to colleagues"></div>
  <div class="abs welcome-copy">
    <div class="eyebrow">Welcome to</div>
    <h2 class="h">Ninth Bay Capital</h2>
    <p class="lead">Sed ut perspiciatis unde omnis iste natus o sit voluptatem accusantium doloremque laudantium, totam rem aperiam, eaque ipsa quae ab illo inventore veritatis et</p>
    <p class="body">At vero eos et accusamus et iusto odio dignissimos dus qui blanditiis praesentium voluptatum deleniti atque corrupti quos dolores et quas molestias excepturi sint occaecati cupiditate non provident, similique sunt in culpa qui officia deserunt mollitia animi, id est laborum et dolorum fuga. Et harum quidem rerum facilis est et expedita</p>
  </div>
  <div class="btn" style="left:642px;top:421px;width:250px;height:37px">LEARN MORE ABOUT US <svg viewBox="0 0 12 12"><path d="M2 10L10 2M4 2h6v6" fill="none" stroke="currentColor" stroke-width="1.4"/></svg></div>
</section>

<section class="abs services">
  <div class="eyebrow" style="margin-top:66px">Services</div>
  <h2 class="h">What we do</h2>
  <p style="font-size:16px;color:#555">A modular offering so you can choose what fits your transition best.</p>
  <article class="card" style="left:101px">
    <div class="pic" role="img" aria-label="Glowing financial growth chart above a hand" style="background:linear-gradient(160deg,#163349,#0f2233 60%,#2a6a70)"></div>
    <h3>Wealth Planning &amp; Investment</h3>
    <p>Long-term allocation, risk-based planning, investment selection aligned to your goals.</p>
  </article>
  <article class="card" style="left:438px">
    <div class="pic" role="img" aria-label="Team reviewing charts around a wooden table, seen from above" style="background:linear-gradient(160deg,#7d6a3c,#b7933c 50%,#5d5448)"></div>
    <h3>Business Structuring</h3>
    <p>Entity structuring, revenue optimization, and advisory for athlete entrepreneurs.</p>
  </article>
  <article class="card" style="left:775px">
    <div class="pic" role="img" aria-label="Advisors shaking hands with clients at a desk" style="background:linear-gradient(160deg,#c9ccc9,#7d7466 55%,#2d2a28)"></div>
    <h3>Risk &amp; Insurance</h3>
    <p>Protect what you've built—tailored coverage and planning for peace of mind.</p>
  </article>
</section>

<section class="abs discipline">
  <div class="abs discipline-copy">
    <h2 class="h">From discipline to<br>financial discipline</h2>
    <p>We translate the structure, routines, and discipline that created your success into actionable financial plans: budget, investment, business growth, and legacy planning.</p>
  </div>
  <div class="btn outline" style="left:101px;top:296px;width:192px;height:37px">BOOK A SESSION <svg viewBox="0 0 12 12"><path d="M2 10L10 2M4 2h6v6" fill="none" stroke="currentColor" stroke-width="1.4"/></svg></div>
  <div class="abs discipline-photo" role="img" aria-label="Two colleagues smiling over a tablet in an office"></div>
</section>

<section class="abs why">
  <div class="abs why-photo" role="img" aria-label="Team meeting around a long white table, seen from above"></div>
  <div class="abs why-frame"></div>
  <div class="abs why-copy">
    <div class="eyebrow">Why us</div>
    <h2 class="h">Why Ninth Bay Capital?</h2>
    <p class="intro">Ninth Bay is the season after the game. We bring structured planning, a disciplined approach, and a long-term mindset.</p>
    <dl>
      <dt>Structured plans</dt><dd>clear milestones and financial KPIs</dd>
      <dt>Holistic advice</dt><dd>investments, tax, business, insurance</dd>
      <dt>Legacy focus</dt><dd>multigenerational thinking</dd>
    </dl>
  </div>
  <div class="btn" style="left:636px;top:439px;width:157px;height:37px">CONTACT US <svg viewBox="0 0 12 12"><path d="M2 10L10 2M4 2h6v6" fill="none" stroke="currentColor" stroke-width="1.4"/></svg></div>
</section>

<section class="abs contact">
  <div class="abs contact-copy">
    <div class="eyebrow">Contact us</div>
    <h2 class="h">Get in touch</h2>
    <p class="sub">There are many variations of passages of Lorem Ipsum available, but the</p>
    <div class="info"><svg viewBox="0 0 24 24"><path d="M12 2a7 7 0 0 0-7 7c0 5 7 13 7 13s7-8 7-13a7 7 0 0 0-7-7zm0 10a3 3 0 1 1 0-6 3 3 0 0 1 0 6z" fill="#1e1e1e"/></svg><span>48 Harbor Ln<br>Bayview, US 20418</span></div>
    <div class="info"><svg viewBox="0 0 24 24"><path d="M2 5h20v14H2z M2 5l10 8 10-8" fill="none" stroke="#1e1e1e" stroke-width="2"/></svg><span>info@ninthbaycapital.com</span></div>
    <div class="info"><svg viewBox="0 0 24 24"><path d="M5 3l4 1 1 4-2 2a12 12 0 0 0 6 6l2-2 4 1 1 4-2 2C10 21 3 14 3 5z" fill="none" stroke="#1e1e1e" stroke-width="2"/></svg><span>+1 555 014 2290</span></div>
  </div>
  <form class="abs form">
    <h3>LET'S TALK</h3>
    <div class="field" style="left:28px;top:90px;width:229px;height:42px">Full Name</div>
    <div class="field" style="left:264px;top:90px;width:229px;height:42px">Phone</div>
    <div class="field" style="left:28px;top:142px;width:465px;height:42px">Email Address</div>
    <div class="field" style="left:28px;top:193px;width:465px;height:94px">Write Your Message Here</div>
    <div class="btn" style="left:187px;top:308px;width:114px;height:36px">SUBMIT <svg viewBox="0 0 12 12"><path d="M2 10L10 2M4 2h6v6" fill="none" stroke="currentColor" stroke-width="1.4"/></svg></div>
  </form>
</section>

<footer class="abs site-footer">Copyright ©2025 Ninth Bay Capital. All Rights Reserved.</footer>
</body>
</html>
```